PostCard Design Project

I am making a mailing postcard
I am having the mailing printed using 4 color foil on certain parts.
I am looking for a design that maximizes the foil process where certain parts are done in foil to grab the customers attention (example: if there is a car on the postcard the headlights would be done in foil) .
I am targeting some industries, (auto, real estate, medical, beauty) I would like the post card to have examples of postcard ideas for 2 or 3 of these industries.
specs:
the postcard should be atleast 6.5x9 up to 8.5x11, I don't want to restrict the space for the creative as I don't want everything to look like a huge mess. both sides will be used.
the piece is a direct mail piece so it has to meet requirements of https://www.mailvantor.com/business/pdf/quick-reference-guide.pdf
text will be
"business with no limits, meet mailing with no addresses, gain new customers through "Open Porch Route Drop" reach new customers at their home without needing their address. "
I also want some current print specials I am running included.
-double your order FREE (order 500 business cards and get 1000)
-250 100lb gloss stock brochures 99.00
-business packages (cards, envelopes and letterhead) 299
-1000 flyers 140.40
-5000 postcards 179.99
A list of services
banners
booklets
brochures
business cards
calendars
catalogs
CD/DVD packages
envelopes
event tickets
flyers
hangtags
postcards
posters
presentation folders
rack cards
labels
table tents
window cling and decal
"order 24/7 orders@inkwillow.com" must be included
my logo is InkWillow will be supplied later
ive received some great designs. however Im looking for something a little more modern like some zorvel would put out. if the amount of words is too much please feel free to edit. also an idea i had for the list of services i offer is to have it transparent yet readable as the background of the postcard some small some big but covering the entire backgroud. you can then design on top of that with other thing. just an early morning thought
Reason: I have uploaded a sketch of my idea, please take time to look at it for an accurate depiction of what im looking for. feel free to add elements that make it pop off the page
Reason: We are getting close i will be providing feed back today

```html
<!DOCTYPE html>
<html lang="en">
<head>
<meta charset="utf-8">
<title>InkWillow Postcard – Front and Back</title>
<link rel="stylesheet" href="https://fonts.googleapis.com/css2?family=Archivo+Black&family=Open+Sans:wght@400;600;700&display=swap">
<style>
  :root {
    --page-bg: #e7e4df;
    --sky-blue: #1ba4dd;
    --ink-black: #0b0b0b;
    --band-black: #060606;
    --lime: #e2ea3b;
    --cyan: #2ba9e1;
    --white: #ffffff;
    --soft-grey: #b5b5b5;
    --band-grey-top: #5c5c5c;
    --band-grey-bottom: #2c2c2c;
  }
  * { box-sizing: border-box; margin: 0; padding: 0; }
  html, body {
    width: 1200px; height: 900px; overflow: hidden;
    background: var(--page-bg);
    font-family: "Open Sans", Arial, sans-serif;
  }
  .postcard-set {
    position: absolute; inset: 0;
    display: flex; align-items: center; justify-content: center; gap: 30px;
  }
  .postcard {
    position: relative; width: 560px; height: 400px; overflow: hidden;
    box-shadow: 0 10px 24px rgba(0,0,0,0.25);
  }

  /* ---------- Front ---------- */
  .postcard-front { background: var(--sky-blue); }
  .front-band {
    position: absolute; left: 0; right: 0; bottom: 0; height: 68px;
    background: var(--band-black);
    display: flex; align-items: center; justify-content: flex-end; padding-right: 22px;
  }
  .brand-name {
    font-family: "Open Sans", Arial, sans-serif; font-weight: 600;
    color: var(--lime); letter-spacing: 1px; white-space: nowrap;
  }
  .front-band .brand-name { font-size: 30px; }

  .sample-ad { position: absolute; }
  .sample-ad-jewelry {
    left: 246px; top: 70px; width: 150px; height: 190px;
    background: linear-gradient(160deg, #7a7a7a, #2b2b2b);
  }
  .sample-ad-beauty {
    left: 372px; top: 0; width: 188px; height: 118px;
    background: linear-gradient(120deg, #f1f4f7 0%, #d9c3b2 55%, #7fb6d9 100%);
  }
  .sample-ad-auto {
    left: 318px; top: 110px; width: 216px; height: 208px;
    background: linear-gradient(150deg, #f2f2f2 0%, #f2f2f2 18%, #d3202a 30%, #8f0f16 70%, #1a1a1a 100%);
    box-shadow: -4px 4px 10px rgba(0,0,0,0.35);
  }

  .headline {
    position: absolute; left: 22px; top: 92px;
    font-family: "Archivo Black", "Arial Black", sans-serif;
    color: var(--white); line-height: 1.02; font-size: 30px;
    text-shadow: 1px 1px 0 #555, 2px 2px 0 #444, 3px 3px 0 #333, 4px 4px 6px rgba(0,0,0,0.5);
  }
  .headline .accent { color: var(--lime); }
  .headline .headline-shine { font-size: 54px; line-height: 1; }
  .front-contact {
    position: absolute; left: 26px; top: 282px;
    color: var(--white); font-weight: 700; font-size: 18px; line-height: 1.2;
  }

  /* ---------- Back ---------- */
  .postcard-back {
    background: linear-gradient(180deg, #141414 0%, var(--ink-black) 60%, #1c1c1c 100%);
  }
  .service-list {
    position: absolute; left: 16px; top: 8px;
    list-style: none; line-height: 1.02; color: var(--white);
  }
  .service-list li { white-space: nowrap; }
  .tone-cyan { color: var(--cyan); }
  .tone-lime { color: var(--lime); }

  .back-brand { position: absolute; left: 150px; top: 58px; }
  .back-brand .brand-name { font-size: 28px; }

  .stamp-box {
    position: absolute; right: 24px; top: 14px; width: 58px; height: 38px;
    background: var(--white);
  }
  .address-box {
    position: absolute; right: 24px; top: 62px; width: 212px; height: 128px;
    background: var(--white);
  }

  .special {
    position: absolute; right: 0;
    background: linear-gradient(180deg, var(--band-grey-top), var(--band-grey-bottom));
    color: var(--white); font-size: 11.5px; font-weight: 600; line-height: 1.3;
    text-align: center; padding: 3px 10px;
  }
  .special-1 { top: 204px; width: 300px; }
  .special-2 { top: 262px; width: 252px; }
  .special-3 { top: 302px; width: 196px; }
  .special-4 { top: 326px; width: 166px; }

  .route-drop-note {
    position: absolute; right: 14px; top: 352px;
    color: var(--soft-grey); font-size: 11px; font-weight: 600; white-space: nowrap;
  }
  .route-drop-note .tone-lime { font-weight: 700; }

  .back-footer {
    position: absolute; left: 0; right: 0; bottom: 0; height: 28px;
    background: linear-gradient(90deg, rgba(80,80,80,0) 30%, #5a5a5a 100%);
    color: #cfcfcf; font-size: 12px;
    display: flex; align-items: center; justify-content: flex-end; padding-right: 14px;
  }
</style>
</head>
<body>
<main class="postcard-set">

  <section class="postcard postcard-front" aria-label="Postcard front">
    <div class="sample-ad sample-ad-jewelry" role="img" aria-label="Sample jewelry advertisement with diamond rings"></div>
    <div class="sample-ad sample-ad-beauty" role="img" aria-label="Sample beauty advertisement with a smiling model"></div>
    <div class="sample-ad sample-ad-auto" role="img" aria-label="Sample auto advertisement showing the front of a red sports car"></div>

    <h1 class="headline">
      PRINTING<br>
      THAT <span class="accent">MAKES</span><br>
      YOUR<br>
      <span class="accent">BUSINESS</span><br>
      <span class="headline-shine">SHINE !</span>
    </h1>
    <p class="front-contact">24 hr/7 Day<br>orders@inkwillow.com</p>

    <div class="front-band"><span class="brand-name">InkWillow</span></div>
  </section>

  <section class="postcard postcard-back" aria-label="Postcard back">
    <ul class="service-list">
      <li class="tone-cyan" style="font-size:11px">Banner</li>
      <li style="font-size:13px">booklets</li>
      <li style="font-size:14px">brochures</li>
      <li class="tone-lime" style="font-size:13px">Buisness cards</li>
      <li style="font-size:18px">Calanders</li>
      <li style="font-size:22px">Catalougs</li>
      <li class="tone-cyan" style="font-size:34px">Envelops</li>
      <li style="font-size:17px">Presentation Folder</li>
      <li class="tone-lime" style="font-size:30px">Event Tickets</li>
      <li style="font-size:18px">Window cling and Decal</li>
      <li style="font-size:18px">CD/DVD Packages</li>
      <li class="tone-lime" style="font-size:30px">rack Cards</li>
      <li style="font-size:22px">Table tents</li>
      <li class="tone-cyan" style="font-size:34px">Flyers</li>
      <li style="font-size:16px">Hantags</li>
      <li class="tone-lime" style="font-size:14px">postcard</li>
      <li style="font-size:12px">Posters</li>
    </ul>

    <div class="back-brand"><span class="brand-name">InkWillow</span></div>

    <div class="stamp-box" aria-label="Postage area"></div>
    <div class="address-box" aria-label="Mailing address area"></div>

    <p class="special special-1">Double your order FREE<br>(order 500 business cards and get 1000)<br>250 100lb gloss stock brochures 99.00</p>
    <p class="special special-2">Business packages<br>(cards, envelopes and letterhead) 299</p>
    <p class="special special-3">1000 flyers 140.40</p>
    <p class="special special-4">5000 postcards 179.99</p>

    <p class="route-drop-note">Reach new customers at home with <span class="tone-lime">“Open Porch Route Drop”</span></p>

    <p class="back-footer">24 hr/7 Day orders@inkwillow.com</p>
  </section>

</main>
</body>
</html>
```